Dovecote Realty

Business cards for 4 people

They need to say for all
87 Tarrow Quay, Boston MA 02114

Each person will have their own personal information
We would like gold embossing for the name of the company
Marla is the blonde sitting in the chair smiling her information should be on the back of the card with her name and information
Should say for slogan classic pattern, elevated experience
grace@dovecoteprops.com
(413) 555-0182

Odette is the brunette with wavy hair in the tan suit odette@dovecoteprops.com
(617) 555-0137

faith@dovecoteprops.com
(413) 555-0164
standing next to the chair

hope@dovecoteprops.com
(413) 555-0199
close up headshot

```html
<!DOCTYPE html>
<html lang="en">
<head>
<meta charset="utf-8">
<title>Dovecote Realty — Business Card</title>
<link href="https://fonts.googleapis.com/css2?family=Open+Sans:wght@400;600;700&display=swap" rel="stylesheet">
<style>
  :root {
    --backdrop: #222223;
    --card: #1f2024;
    --card-edge: #17181b;
    --gold: #e2b357;
    --ink: #f2f2f2;
    --muted-mark: #34353b;
    --photo-dark: #2a2623;
    --photo-warm: #9a6a45;
  }
  * { box-sizing: border-box; margin: 0; padding: 0; }
  html, body { width: 1200px; height: 780px; overflow: hidden; }
  body {
    background: var(--backdrop);
    font-family: "Open Sans", Arial, sans-serif;
    display: flex;
    align-items: center;
    justify-content: center;
    gap: 48px;
  }
  .card {
    position: relative;
    width: 540px;
    height: 309px;
    background: var(--card);
    border: 1px solid var(--card-edge);
    overflow: hidden;
  }

  /* Front */
  .card-front .portrait {
    position: absolute;
    left: 0; top: 40px;
    width: 240px; height: 269px;
    background: radial-gradient(ellipse at 55% 35%, var(--photo-warm) 0%, #6e4a30 40%, var(--photo-dark) 75%, var(--card) 100%);
  }
  .brand {
    position: absolute;
    right: 34px; top: 28px;
    display: flex; align-items: center; gap: 10px;
  }
  .brand-name {
    color: var(--gold);
    font-weight: 600;
    font-size: 17px;
    letter-spacing: 2px;
    text-transform: uppercase;
  }
  .brand-dot {
    width: 52px; height: 52px;
    border: 2px solid var(--gold);
    border-radius: 50%;
  }
  .person {
    position: absolute;
    right: 34px; top: 106px;
    text-align: right;
  }
  .person-name {
    color: var(--gold);
    font-weight: 700;
    font-size: 27px;
    line-height: 1.1;
    white-space: nowrap;
  }
  .person-title {
    color: var(--ink);
    font-size: 10.5px;
    margin-top: 2px;
  }
  .accent-bar {
    position: absolute;
    right: 0; top: 108px;
    width: 22px; height: 40px;
    background: var(--gold);
  }
  .address {
    position: absolute;
    right: 34px; top: 176px;
    text-align: right;
    color: var(--ink);
    font-size: 15px;
    line-height: 1.25;
  }
  .contacts {
    position: absolute;
    right: 16px; top: 222px;
    list-style: none;
    color: var(--ink);
    font-size: 14.5px;
    line-height: 1.3;
  }
  .contacts li {
    display: flex; align-items: center; justify-content: flex-end; gap: 6px;
  }
  .contacts svg { width: 12px; height: 12px; fill: none; stroke: var(--gold); stroke-width: 1.6; }

  /* Back */
  .card-back {
    display: flex; align-items: center; justify-content: center; gap: 18px;
  }
  .card-back .brand-name { color: var(--muted-mark); font-size: 30px; letter-spacing: 4px; }
  .card-back .brand-dot { width: 96px; height: 96px; border-color: var(--muted-mark); }
</style>
</head>
<body>
  <section class="card card-front" aria-label="Card front">
    <div class="portrait" role="img" aria-label="Portrait photo of Odette, brunette with wavy hair in a tan suit"></div>
    <div class="brand">
      <span class="brand-name">Dovecote Realty</span>
      <span class="brand-dot"></span>
    </div>
    <div class="accent-bar"></div>
    <div class="person">
      <p class="person-name">Odette Marchand</p>
      <p class="person-title">Real Estate Advisor and Sales Manager</p>
    </div>
    <p class="address">87 Tarrow Quay,<br>Boston MA 02114</p>
    <ul class="contacts">
      <li>(617) 555-0137
        <svg viewBox="0 0 12 12"><path d="M3 1.5 L4.5 4 L3.5 5 Q4.5 7.5 7 8.5 L8 7.5 L10.5 9 L9.5 10.5 Q4 10 1.5 3 Z"/></svg>
      </li>
      <li>www.dovecoteprops.com
        <svg viewBox="0 0 12 12"><circle cx="6" cy="6" r="4.8"/><ellipse cx="6" cy="6" rx="2" ry="4.8"/><path d="M1.2 6 H10.8"/></svg>
      </li>
      <li>odette@dovecoteprops.com
        <svg viewBox="0 0 12 12"><rect x="1" y="2.5" width="10" height="7"/><path d="M1 2.5 L6 6.5 L11 2.5"/></svg>
      </li>
    </ul>
  </section>

  <section class="card card-back" aria-label="Card back">
    <span class="brand-name">Dovecote Realty</span>
    <span class="brand-dot"></span>
  </section>
</body>
</html>
```